New website: Wanderfjordia.com

We need to build a website for our small travel agency.
We want to be able to upload our brochures and offer our tours on site. No online payments involved yet.

We want to create an exact copy of another website: www.trekvalora.is, but with our own information and products. We like that design very much.

We are not going to do any sales via the website as the website above, but instead we want to show in the same style and everything the different tours that we offer.

We need to be able to modify tours: tour pictures, info, add videos, text, etc.

We need the website in English and Spanish. We can provide the Spanish translation.

We would advice you to create a copy of that website, with the text to be editable by us.
We own the website www.wanderfjordia.com and need that the designer uploads it and makes it work as well.

We have uploaded some pictures that can be used as place markers.

I HAVE UPLOADED OUR BROCHURE DEMO SO YOU CAN GET MORE INFO IN ENGLISH ABOUT US AND MORE PICTURES.

PLEASE REMEMBER THAT THE WEBSITE ¨MOVES¨ when you resize it! Specially the pictures get ¨bigger¨ or smaller¨ when you resize. The same applies to the logos :-)

Once you have created the front page just as the original website I will select it and then we can put the real info and extra pages :-)

Tourists, international people traveling.

Tourism

Coded - Design and coding required

5+ page

Sans Serif

ffffff

• Exactly the same layout of the website mentioned (www.trekvalora.is)
• Everything the same, but with our own logo, texts and photos.
• HOME
• TOURS
• GROUPS
• OUR MOST POPULAR TOURS

```html
<!DOCTYPE html>
<html lang="en">
<head>
<meta charset="utf-8">
<title>Wanderfjordia – Home</title>
<link href="https://fonts.googleapis.com/css2?family=Noto+Serif:ital,wght@0,400;0,700;1,400&family=Open+Sans:wght@400;600;700&display=swap" rel="stylesheet">
<style>
:root{
  --black:#000;
  --white:#fff;
  --ink:#1a1a1a;
  --text:#333;
  --accent:#c8242b;
  --band-gray:#ebebe9;
  --band-cream:#f5f5f1;
  --band-light:#f3f3f3;
  --rule:#dcdcdc;
}
*{margin:0;padding:0;box-sizing:border-box}
html,body{width:1200px;height:3203px;overflow:hidden;background:var(--white)}
body{font-family:"Open Sans",Arial,sans-serif;color:var(--text);position:relative}
h1,h2,h3{font-weight:400}
.abs{position:absolute}

/* header */
.site-header{position:absolute;left:0;top:0;width:1200px;height:79px;background:var(--black)}
.brand{position:absolute;left:148px;top:26px;color:var(--white);font-weight:700;font-size:20px;letter-spacing:1px;display:flex;align-items:center;gap:8px}
.brand .dot{width:10px;height:10px;border-radius:50%;background:var(--accent)}
.main-nav{position:absolute;left:496px;top:31px;display:flex;gap:26px;font-size:13px;color:var(--white);text-transform:uppercase}
.nav-tools{position:absolute;left:962px;top:32px;display:flex;gap:14px;align-items:center}
.lang{width:16px;height:10px;background:#8a8ab0;display:inline-block}
.lang.es{background:#e0a020}

/* hero */
.hero-tile{position:absolute;overflow:hidden}
.hero-tile .caption{position:absolute;right:18px;bottom:18px;text-align:right;color:var(--white);font-family:"Noto Serif",Georgia,serif;font-style:italic;text-shadow:0 1px 3px rgba(0,0,0,.35)}
.caption .big{font-size:32px;line-height:1.15}
.caption .small{font-size:19px}

/* welcome */
.welcome-title{position:absolute;left:0;width:1200px;top:515px;text-align:center;font-family:"Noto Serif",Georgia,serif;font-size:29px;color:var(--ink);letter-spacing:.5px}
.welcome-text{position:absolute;left:160px;width:880px;top:588px;text-align:center;font-size:11.5px;line-height:19px;color:var(--ink)}
.popular-title{position:absolute;left:0;width:1200px;top:638px;text-align:center;font-family:"Noto Serif",Georgia,serif;font-size:21px;color:var(--ink)}
.tour-tabs{position:absolute;left:210px;width:780px;top:682px;display:flex;justify-content:center;gap:24px;font-size:13px;color:var(--ink);border-bottom:1px solid var(--rule);padding-bottom:10px}
.tour-tabs .active{color:var(--accent);border-bottom:2px solid var(--accent);padding-bottom:8px;margin-bottom:-11px}

/* tours */
.tour-card{position:absolute;width:273px}
.tour-card .photo{width:273px;height:228px}
.tour-card h3{font-family:"Noto Serif",Georgia,serif;font-size:20px;color:var(--ink);margin:12px 0 4px 6px}
.tour-card .length{font-size:12.5px;color:var(--ink);margin-left:6px}
.tour-card .price{font-size:12.5px;color:var(--accent);margin-left:6px;margin-top:2px}

/* info bands */
.band{position:absolute;left:0;width:1200px;overflow:hidden}
.band h2{font-family:"Noto Serif",Georgia,serif;font-size:29px;color:var(--ink);letter-spacing:.5px;margin-bottom:16px}
.band p{font-size:12.5px;line-height:20px;color:var(--ink);text-align:justify}
.btn{display:inline-block;margin-top:24px;border:1.5px solid var(--accent);color:var(--accent);font-size:14.5px;padding:10px 20px;background:transparent}
.feature-image{position:absolute}

/* partners */
.partner{position:absolute;background:#bdbdbd}

/* footer */
.site-footer{position:absolute;left:0;top:2925px;width:1200px;height:278px;background:var(--black);color:var(--white)}
.footer-logo{position:absolute;left:176px;top:52px;width:112px;height:112px;border:3px solid var(--white);border-radius:50%;display:flex;align-items:center;justify-content:center;font-weight:700;font-size:12px;letter-spacing:.3px}
.footer-col{position:absolute;top:48px;font-size:12.5px;line-height:24px;text-transform:uppercase}
.copyright{position:absolute;left:152px;top:225px;font-size:10px}
.social{position:absolute;left:836px;top:233px;display:flex;gap:18px}
.social span{width:14px;height:14px;border-radius:3px;background:var(--white);display:block}
</style>
</head>
<body>

<header class="site-header">
  <div class="brand"><span class="dot"></span>WANDERFJORDIA</div>
  <nav class="main-nav"><span>Home</span><span>Tours</span><span>Groups</span><span>Rent a car</span><span>Flight</span><span>Contact</span></nav>
  <div class="nav-tools">
    <svg width="13" height="13" viewBox="0 0 13 13"><circle cx="5.5" cy="5.5" r="4" fill="none" stroke="#fff" stroke-width="2"/><line x1="8.5" y1="8.5" x2="12" y2="12" stroke="#fff" stroke-width="2"/></svg>
    <span class="lang"></span><span class="lang es"></span>
  </div>
</header>

<section class="hero">
  <div class="hero-tile" style="left:132px;top:96px;width:536px;height:399px;background:linear-gradient(180deg,#4f86c8 0%,#8fb2da 28%,#dfe6ee 42%,#7d8896 52%,#4a5868 64%,#6f7a72 78%,#3a3f3c 100%)" role="img" aria-label="Travellers before granite mountain peaks">
    <div class="caption"><div class="big">Scenery</div><div class="small">Wanderfjordia</div></div>
  </div>
  <div class="hero-tile" style="left:683px;top:96px;width:385px;height:190px;background:linear-gradient(180deg,#6f95c4 0%,#c8d4e0 40%,#7c8890 55%,#7b845c 70%,#4f5a3c 100%)" role="img" aria-label="Open steppe with distant hills">
    <div class="caption"><div class="big">Magallanes</div><div class="small">Wanderfjordia</div></div>
  </div>
  <div class="hero-tile" style="left:683px;top:305px;width:385px;height:190px;background:linear-gradient(180deg,#8ea6c2 0%,#dfe4ea 40%,#9aa4ac 55%,#5c6f7c 66%,#46533f 100%)" role="img" aria-label="Lake under a cloudy sky">
    <div class="caption"><div class="big">Nature</div><div class="small">Wanderfjordia</div></div>
  </div>
</section>

<h1 class="welcome-title">WELCOME TO WANDERFJORDIA</h1>
<svg class="abs" style="left:590px;top:560px" width="20" height="26" viewBox="0 0 20 26"><path d="M10 0C4.5 0 0 4.3 0 9.6 0 16.8 10 26 10 26s10-9.2 10-16.4C20 4.3 15.5 0 10 0z" fill="#111"/><circle cx="10" cy="9.5" r="4" fill="#c8242b"/></svg>
<p class="welcome-text">Wanderfjordia es un nuevo tour operator receptivo de confianza especializado en el diseño y prestación de servicios personalizados de incoming en destinos prístinos de la Ecorregión Sub-Antártica y Antártica Chilena.</p>

<h2 class="popular-title">Our most popular tours</h2>
<nav class="tour-tabs"><span class="active">Popular Tours</span><span>Day Tours</span><span>Travel by Air Tours</span><span>Self Drive Tours</span><span>Adventures Tours</span><span>Customize Tours</span><span>Transfer</span></nav>

<section class="tours">
  <article class="tour-card" style="left:169px;top:741px"><div class="photo" role="img" aria-label="Road toward mountain peaks" style="background:linear-gradient(180deg,#6f97c8 0%,#c9d6e2 35%,#6f7682 50%,#9a8a4c 66%,#b3752e 80%,#5a5548 100%)"></div><h3>Ullamco laboris</h3><div class="length">length: 3 - 5 hours</div><div class="price">6.400 ISK</div></article>
  <article class="tour-card" style="left:463px;top:741px"><div class="photo" role="img" aria-label="Hiker on a lakeside ridge" style="background:linear-gradient(180deg,#4f86cc 0%,#b8cce2 30%,#58677a 45%,#3d8aa8 60%,#2f6e86 72%,#5a5244 85%,#3b3630 100%)"></div><h3>Ullamco laboris</h3><div class="length">length: 3 - 5 hours</div><div class="price">6.400 ISK</div></article>
  <article class="tour-card" style="left:758px;top:741px"><div class="photo" role="img" aria-label="Turquoise lake below peaks" style="background:linear-gradient(180deg,#5f95d6 0%,#c4d4e6 30%,#eef1f4 42%,#6e7a80 52%,#3fb6bc 66%,#2e9aa0 76%,#55603e 100%)"></div><h3>Ullamco laboris</h3><div class="length">length: 3 - 5 hours</div><div class="price">6.400 ISK</div></article>
  <article class="tour-card" style="left:169px;top:1070px"><div class="photo" role="img" aria-label="Cloudy sky over plains" style="background:linear-gradient(180deg,#7e9cc0 0%,#d6dde6 40%,#a7b2bc 58%,#5c6a55 72%,#3f4a38 100%)"></div><h3>Ullamco laboris</h3><div class="length">length: 3 - 5 hours</div><div class="price">6.400 ISK</div></article>
  <article class="tour-card" style="left:463px;top:1070px"><div class="photo" role="img" aria-label="Lodge beside a blue lake" style="background:linear-gradient(180deg,#2f6fc0 0%,#8fb4e0 30%,#e6ecf2 48%,#6f8aa0 56%,#2f6d98 70%,#3a6f94 80%,#55613f 100%)"></div><h3>Ullamco laboris</h3><div class="length">length: 3 - 5 hours</div><div class="price">6.400 ISK</div></article>
  <article class="tour-card" style="left:758px;top:1070px"><div class="photo" role="img" aria-label="Mountain road under clouds" style="background:linear-gradient(180deg,#3f7ac6 0%,#d0dcea 38%,#8a96a2 55%,#4e5a58 70%,#2f3530 100%)"></div><h3>Ullamco laboris</h3><div class="length">length: 3 - 5 hours</div><div class="price">6.400 ISK</div></article>
</section>

<section class="band about" style="top:1396px;height:472px;background:var(--band-gray)">
  <div class="feature-image" style="left:683px;top:0;width:517px;height:472px;background:linear-gradient(160deg,#e9e9e6 0%,#cfcfcb 30%,#6b6b6b 48%,#3a3a3a 58%,#d9d9d5 72%,#f0f0ee 85%,#2c2c2c 100%)" role="img" aria-label="Camera, notebook and coffee on a wooden desk"></div>
  <div class="abs" style="left:213px;top:120px;width:417px">
    <h2>QUIENES SOMOS</h2>
    <p>Somos una empresa conformada por un idóneo equipo de trabajo que consta de alta motivación, óptimo entrenamiento, elevado capital humano y cuyos integrantes poseen más de 10 años de experiencia trabajando en forma independiente en Turismo Receptivo Regional, Nacional e Internacional. En conjunto nos potenciamos y logramos satisfacer las altas demandas de servicios turísticos requeridos por nuestros clientes.</p>
    <span class="btn">More About Groups</span>
  </div>
</section>

<section class="band mission" style="top:1868px;height:463px;background:var(--band-cream)">
  <div class="feature-image" style="left:0;top:0;width:502px;height:463px;background:linear-gradient(200deg,#ffffff 0%,#f2e2c2 18%,#d9913c 35%,#8a8a5a 50%,#e8742a 65%,#c75a1e 78%,#f6f4ee 92%)" role="img" aria-label="Stacked suitcases with a travel sign"></div>
  <div class="abs" style="left:576px;top:142px;width:416px">
    <h2>MISION</h2>
    <p>Nuestra misión es ofrecer servicios de Turismo Receptivo para la Región de Magallanes y Antártica Chilena que cumplan con las exigencias de calidad y valor humano que nuestros clientes solicitan. Para lograrlo, trabajamos en conjunto con proveedores turísticos seleccionados y nos enfocamos hacia la excelencia de un servicio personalizado, sirviendo con pasión, experiencia y responsabilidad a cada uno de nuestros clientes.</p>
    <span class="btn">Contact Us for more info</span>
  </div>
</section>

<section class="band vision" style="top:2331px;height:445px;background:var(--band-light)">
  <div class="feature-image" style="left:640px;top:0;width:560px;height:445px;background:linear-gradient(170deg,#f3f3f3 0%,#9fcbe9 18%,#4f9ed6 32%,#c98a4a 45%,#9a4d22 60%,#e9c48a 78%,#f3f3f3 95%)" role="img" aria-label="Beach suitcase with hat and palm leaves"></div>
  <div class="abs" style="left:205px;top:115px;width:416px">
    <h2>VISION</h2>
    <p>Nuestra visión es crear una Plataforma de Servicios Logísticos y Turísticos para la Ecorregión Sub-Antártica y Antártica que una toda la oferta turística de la zona a través de una red local, nacional y global de proveedores, con el objetivo de mejorar, a través de la cuidadosa selección de prestadores, la accesibilidad por parte del cliente, la competitividad dentro del mercado, facilitando la inclusión de pequeñas y medianas empresas.</p>
    <span class="btn">Contact Us</span>
  </div>
</section>

<section class="partners">
  <div class="partner" style="left:368px;top:2826px;width:72px;height:72px;border-radius:50%"></div>
  <div class="partner" style="left:570px;top:2826px;width:50px;height:72px;background:#9a9a9a"></div>
  <div class="partner" style="left:762px;top:2836px;width:78px;height:52px"></div>
</section>

<footer class="site-footer">
  <div class="footer-logo">WANDERFJORDIA</div>
  <div class="footer-col" style="left:414px">Home<br>Tours<br>Groups<br>Rent a car<br>Flight<br>Contact</div>
  <div class="footer-col" style="left:604px">How to book<br>Booking terms<br>Privacy policy</div>
  <div class="footer-col" style="left:835px">Wanderfjordia<br>Brekkustigur 42<br>104 Valora, Fjordland<br>+354 555 0142<br>info@wanderfjordia.com<br>www.wanderfjordia.com<br>View on map</div>
  <div class="copyright">Copyright© 2016. All Rights Reserved.</div>
  <div class="social"><span></span><span></span><span></span><span></span><span></span></div>
</footer>

</body>
</html>
```